Dynamic Business Card for Sports Supplements Company

Hi! I'm looking for an awesome business card to match my existing sports supplement company. I have uploaded my current company logo and screenshot of the front page of my website.

I would like to have something dynamic and interesting and utilize the colors in the website - the reds and purples

The business card should be double sided and focus on a unique eye-catching design on the back and include all the relevant company info.

Most importantly, it should say somewhere: "Sign up on our website for a coupon code."

Target Market(s)

Mostly for women gym goers but it shouldn't be too feminine. It should be in keeping with the website design. It should flow and clearly be connected to it

Industry/Entity Type

Business

Contact Information for Business Card

Lorraine K. Vestal
CEO
LVestal@Quorvanexco.com
www.quorvanexco.com
555.417.3820
P.O. Box 47315
Harlow, Oregon 00000

Sign up on our website for a coupon code

Font styles to use
Serif
Sans Serif
Other font styles liked:
• Novecento font family and "Quorvanex" is in AR Destine font

Requirements
Must have
• One side should be a bold Quorvanex logo design. Even just the symbol itself may be o.k. (see attached file)

```html
<!DOCTYPE html>
<html lang="en">
<head>
<meta charset="utf-8">
<title>Quorvanex Business Card</title>
<link rel="stylesheet" href="https://fonts.googleapis.com/css2?family=Open+Sans:wght@400;700&display=swap">
<style>
  :root {
    --charcoal: #262626;
    --brand-red: #e41c26;
    --paper: #ffffff;
    --ink: #222222;
    --backdrop: #e9e7e4;
  }
  * { margin: 0; padding: 0; box-sizing: border-box; }
  html, body {
    width: 1200px; height: 900px; overflow: hidden;
    background: var(--backdrop);
    font-family: "Open Sans", Arial, sans-serif;
  }
  .canvas { position: relative; width: 1200px; height: 900px; }

  .card { position: absolute; overflow: hidden; }
  .card-front { left: 78px; top: 34px; width: 588px; height: 364px; background: var(--paper); }
  .card-back { left: 388px; top: 505px; width: 567px; height: 352px; background: var(--charcoal); }

  .chevron { position: absolute; inset: 0; }

  .brand { position: absolute; left: 0; right: 0; text-align: center; color: var(--paper); }
  .brand-mark {
    display: block; margin: 0 auto; width: 40px; height: 40px;
    background: var(--brand-red);
  }
  .brand-name {
    display: block; font-weight: 700; font-size: 34px; letter-spacing: 1px;
    line-height: 1; margin-top: 16px;
  }
  .brand-tagline {
    display: block; font-weight: 400; font-size: 11.5px; letter-spacing: 2.2px;
    line-height: 1; margin-top: 6px;
  }
  .card-front .brand { top: 66px; }
  .card-back .brand { top: 82px; }
  .card-back .brand-mark { width: 52px; height: 52px; }
  .card-back .brand-name { font-size: 38px; margin-top: 40px; }
  .card-back .brand-tagline { font-size: 12.5px; margin-top: 8px; }

  .person { position: absolute; left: 18px; top: 292px; }
  .person-name { color: var(--brand-red); font-size: 17px; line-height: 1.2; }
  .person-title { color: var(--ink); font-size: 14px; margin-top: 6px; }

  .contact { position: absolute; right: 28px; top: 233px; text-align: right; color: var(--ink); font-size: 14px; }
  .contact-address { line-height: 20px; margin-bottom: 11px; }
  .contact-line { display: flex; justify-content: flex-end; align-items: center; gap: 8px; height: 20px; }
  .contact-line svg { width: 10px; height: 10px; fill: var(--brand-red); flex: none; }

  .coupon-band {
    position: absolute; left: 0; right: 0; bottom: 0; height: 60px;
    background: var(--brand-red); color: var(--paper);
    display: flex; align-items: center; justify-content: center;
    font-size: 15.5px; letter-spacing: 0.3px;
  }
</style>
</head>
<body>
<div class="canvas">

  <section class="card card-front" aria-label="Business card front">
    <svg class="chevron" viewBox="0 0 588 364" aria-hidden="true">
      <polygon points="0,0 588,0 588,14 294,341 0,14" fill="var(--brand-red)"/>
      <polygon points="36,0 552,0 294,291" fill="var(--charcoal)"/>
    </svg>

    <div class="brand">
      <span class="brand-mark"></span>
      <span class="brand-name">QUORVANEX</span>
      <span class="brand-tagline">YOUR TRAINING COMPANION</span>
    </div>

    <div class="person">
      <p class="person-name">LORRAINE K. VESTAL</p>
      <p class="person-title">CEO</p>
    </div>

    <div class="contact">
      <p class="contact-address">P.O. Box 47315<br>Harlow, Oregon 00000</p>
      <p class="contact-line">555.417.3820
        <svg viewBox="0 0 10 10"><path d="M2 0.5 L3.8 2.6 L2.9 3.7 C3.5 5 5 6.5 6.3 7.1 L7.4 6.2 L9.5 8 L8.3 9.5 C4.5 9.3 0.7 5.5 0.5 1.7 Z"/></svg>
      </p>
      <p class="contact-line">LVestal@Quorvanexco.com
        <svg viewBox="0 0 10 10"><path d="M0 2 H10 V8.5 H0 Z M0.6 2.4 L5 5.6 L9.4 2.4" stroke="#fff" stroke-width="0.8"/></svg>
      </p>
      <p class="contact-line">www.quorvanexco.com
        <svg viewBox="0 0 10 10"><circle cx="5" cy="5" r="5"/><path d="M1 5 H9 M5 0.5 C3 3 3 7 5 9.5 M5 0.5 C7 3 7 7 5 9.5" stroke="#fff" stroke-width="0.7" fill="none"/></svg>
      </p>
    </div>
  </section>

  <section class="card card-back" aria-label="Business card back">
    <div class="brand">
      <span class="brand-mark"></span>
      <span class="brand-name">QUORVANEX</span>
      <span class="brand-tagline">YOUR TRAINING COMPANION</span>
    </div>
    <p class="coupon-band">SIGN UP ON OUR WEBSITE FOR A COUPON CODE</p>
  </section>

</div>
</body>
</html>
```